Lantern Petals Website v.1 - attract floral shop franchisees

I need a simple information website for my new business. We are a franchisor of flower shops. The overall purpose of the website is to promote the company and the service, especially to potential franchisees and retailers. Only about 4 pages are required including homepage, About, For Supermarkets, For Franchisees, and Contact. No special functions are required except the site will have two separate inquiry forms that must be filled out online and submitted via automated email. Similarly, an email form should be linked from the Contact page. I have a logo and business cards designed by ArtMingle, and I would like the site to have a consistent color scheme and style. The key to design will be to express the joy and love associated with flowers and floral bouquets.
IMPORTANT - I will be exporting the website design to Wordpress CMS in a site hosted by HostNimbus. For smooth integration into WordPress hosted by HostNimbus, the designer should build the site using a WordPress-friendly format. Ideally, they should use HTML, CSS, and PHP. Creating a custom theme or using a page builder that exports to WordPress-compatible files is best. This ensures the site can be easily imported and managed within WordPress.

Target Market(s)

Potential franchisees (existing florists or creative types who might like to own a floral business) and supermarkets who might want us to run their floral department

Industry/Entity Type

Floral retailing

Requirements
Must have
• A brand theme that is beautiful, consistent throughout and builds on the logo design
Nice to have
• Show gender and ethnic diversity in customers and florists. Pictures of happy florists (for franchisees) and pictures of amazing floral department displays (for supermarkets)

```html
<!DOCTYPE html>
<html lang="en">
<head>
<meta charset="utf-8">
<title>Lantern Petals</title>
<link href="https://fonts.googleapis.com/css2?family=Montserrat:wght@300;400;500;600;700&display=swap" rel="stylesheet">
<style>
:root{
  --orange:#f09a1f;
  --green:#05893f;
  --black:#0a0a0a;
  --ink:#1e1e1e;
  --body:#555555;
  --grey:#f3f3f3;
  --white:#ffffff;
}
*{margin:0;padding:0;box-sizing:border-box}
html,body{width:1200px;height:3849px;overflow:hidden;background:var(--white)}
body{font-family:"Montserrat",sans-serif;color:var(--ink);position:relative}
a{text-decoration:none;color:inherit}
.page{position:relative;width:1200px;height:3849px;overflow:hidden}
.abs{position:absolute}

/* header */
.topline{left:0;top:0;width:1200px;height:5px;background:var(--orange);z-index:5}
.brand{display:flex;align-items:center;gap:10px;font-weight:600;color:var(--orange);font-size:22px;z-index:5}
.brand .dot{width:16px;height:16px;border-radius:50%;background:var(--orange)}
.nav{top:44px;left:430px;display:flex;align-items:center;font-size:13px;font-weight:700;color:var(--white);z-index:5}
.nav a.active{color:var(--orange)}
.nav .sep{margin:0 24px}

/* hero */
.hero-photo{left:0;top:0;width:1200px;height:800px;
  background:radial-gradient(ellipse at 75% 35%,#e9d2c0 0%,#b98a6c 30%,#6a4a36 60%,#2e2520 100%)}
.hero-badge{left:112px;top:158px;width:454px;height:454px;border-radius:50%;background:var(--black);border:4px solid var(--green);
  display:flex;flex-direction:column;align-items:center;justify-content:center;text-align:center;color:var(--white)}
.hero-badge .name{font-size:50px;font-weight:600;color:var(--orange);line-height:1.1;margin-top:10px}
.hero-badge .tag{font-size:22px;font-weight:400;line-height:36px;margin-top:34px}
.btn{display:inline-flex;align-items:center;justify-content:center;background:var(--orange);color:var(--white);
  font-weight:600;font-size:14px;border-radius:24px}
.hero-badge .btn{width:186px;height:44px;color:var(--black);margin-top:22px}

/* content blocks */
.round-photo{border-radius:50%;border:3px solid var(--green);overflow:hidden}
.eyebrow{font-size:28px;font-weight:600;color:var(--orange)}
.title{font-size:39px;font-weight:400;color:var(--ink);margin-top:14px}
.rule{width:98px;height:2px;background:var(--green);margin-top:10px}
.copy{font-size:13px;line-height:25.7px;color:var(--body);text-align:justify;margin-top:20px}
.copy p+p{margin-top:13px}
.block .btn{width:186px;height:44px;margin-top:28px}

/* split band */
.band-left{left:0;top:1948px;width:600px;height:547px;background:linear-gradient(180deg,#f29e20,#eb8d12)}
.band-right{left:600px;top:1948px;width:600px;height:547px;background:linear-gradient(180deg,#07913f,#057a35)}
.band-head{left:0;top:2085px;width:1200px;text-align:center;color:var(--white)}
.band-head .k{font-size:27px;font-weight:700}
.band-head .t{font-size:37px;font-weight:300;margin-top:14px}
.band-head .rule{background:var(--white);margin:10px auto 0;width:98px}
.pill{top:2266px;height:83px;display:flex;align-items:center;font-weight:700;font-size:15px;color:var(--white);text-decoration:none}
.pill-left{left:107px;width:460px;background:var(--green);border-radius:42px 0 0 42px;padding-left:34px}
.pill-right{left:630px;width:458px;background:var(--orange);border-radius:0 42px 42px 0;padding-left:100px}
.hub{left:508px;top:2228px;width:170px;height:170px;border-radius:50%;background:var(--white);
  display:flex;align-items:center;justify-content:center;box-shadow:0 0 0 4px rgba(255,255,255,.4)}
.hub .hub-ring{width:146px;height:146px;border-radius:50%;border:3px solid var(--orange);
  display:flex;align-items:center;justify-content:center;text-align:center;
  font-size:17px;font-weight:600;line-height:22px;color:var(--green)}

/* features */
.feature{display:flex;align-items:center;gap:16px;font-size:19px;font-weight:600;color:var(--ink)}
.icon-circle{width:102px;height:102px;border-radius:50%;display:flex;align-items:center;justify-content:center}
.icon-circle.o{background:var(--orange)}
.icon-circle.g{background:var(--green)}

/* footer */
.footer{left:0;top:3560px;width:1200px;height:289px;background:var(--black);color:var(--white);text-align:center}
.footer .brand{justify-content:center;position:static;margin-top:50px}
.foot-nav{display:flex;justify-content:center;align-items:center;font-size:13px;font-weight:700;margin-top:34px}
.foot-nav .sep{margin:0 22px}
.social{display:flex;justify-content:center;gap:10px;margin-top:22px}
.social span{width:36px;height:36px;border-radius:50%;background:var(--white)}
.copyright{font-size:10px;margin-top:22px}
</style>
</head>
<body>
<div class="page">

  <!-- hero -->
  <div class="abs hero-photo" role="img" aria-label="Photo of a smiling mother hugging her child while holding a bouquet of red tulips"></div>
  <div class="abs topline"></div>
  <div class="abs brand" style="left:112px;top:38px"><span class="dot"></span>Lantern Petals</div>
  <nav class="abs nav">
    <a class="active" href="#">HOME</a><span class="sep">|</span>
    <a href="#">ABOUT US</a><span class="sep">|</span>
    <a href="#">FOR SUPERMARKETS</a><span class="sep">|</span>
    <a href="#">FOR FRANCHISEES</a><span class="sep">|</span>
    <a href="#">CONTACT</a>
  </nav>
  <div class="abs hero-badge">
    <div class="name">Lantern Petals</div>
    <div class="tag">FRESH FLOWERS CONVEY<br>BEAUTY AND LOVE</div>
    <a class="btn" href="#">GET STARTED</a>
  </div>
  <svg class="abs" style="left:0;top:660px" width="1200" height="150" viewBox="0 0 1200 150" aria-hidden="true">
    <path d="M0 120 C250 60 450 80 650 95 C850 110 1050 90 1200 35 L1200 150 L0 150Z" fill="var(--orange)"/>
    <path d="M0 140 C250 90 450 100 650 112 C850 124 1050 100 1200 48 L1200 150 L0 150Z" fill="var(--green)"/>
    <path d="M0 150 C250 110 450 112 650 122 C850 132 1050 112 1200 60 L1200 150Z" fill="var(--white)"/>
  </svg>

  <!-- about -->
  <div class="abs" role="img" aria-label="Cartoon bee illustration" style="left:76px;top:810px;width:100px;height:90px;border-radius:50%;background:linear-gradient(135deg,#f3b72a,#2a2a2a)"></div>
  <div class="abs round-photo" role="img" aria-label="Overhead photo of a florist arranging fresh flowers on a wooden table" style="left:110px;top:862px;width:440px;height:440px;background:radial-gradient(circle at 50% 45%,#c9a2a6,#7b5f52 55%,#3d3129)"></div>
  <div class="abs" style="left:379px;top:1174px;width:138px;height:138px;border-radius:50%;background:var(--white);border:3px solid var(--orange)"></div>
  <div class="abs block" style="left:671px;top:882px;width:417px">
    <div class="eyebrow">About Us</div>
    <div class="title">Lantern Petals</div>
    <div class="rule"></div>
    <div class="copy">
      <p>Fresh flowers convey beauty and love, and in our view should become something every person regularly enjoys. Lantern Petals is an entrepreneurial company created to make top quality fresh flowers and professionally-designed bouquets accessible to every consumer at affordable prices.</p>
      <p>Professional florists typically sell the finest quality stems, design the most beautiful bouquets and provide the finest customer service</p>
    </div>
    <a class="btn" href="#">VIEW MORE</a>
  </div>

  <!-- supermarkets -->
  <div class="abs" style="left:0;top:1406px;width:1200px;height:542px;background:var(--grey)"></div>
  <div class="abs" role="img" aria-label="Photo of a woman smelling a vase of orange and red roses" style="left:560px;top:1406px;width:640px;height:542px;background:linear-gradient(90deg,var(--grey) 0%,#e9d6c8 25%,#d88a62 55%,#8c6a55 100%)"></div>
  <div class="abs block" style="left:112px;top:1496px;width:418px">
    <div class="eyebrow">Our Supermarket</div>
    <div class="title">Floral Department</div>
    <div class="rule"></div>
    <div class="copy">
      <p>Lantern Petals works with some of the country's largest and most progressive supermarkets to provide franchisee ownership and operation of their strategically important floral departments. Supermarkets find that Lantern Petals is able to improve their financial outcomes, provide attentive customer service and satisfaction, and lift the quality of the entire store environment.</p>
    </div>
    <a class="btn" href="#">VIEW MORE</a>
  </div>

  <!-- inquiry band -->
  <div class="abs band-left" role="img" aria-label="Soft-focus photo of orange flowers in a field"></div>
  <div class="abs band-right" role="img" aria-label="Soft-focus photo of green tulip silhouettes"></div>
  <div class="abs band-head">
    <div class="k">Our Supermarket</div>
    <div class="t">Floral Department</div>
    <div class="rule"></div>
  </div>
  <a class="abs pill pill-left" href="#">PROFESSIONAL FLORIST FRANCHISE INQUIRY</a>
  <a class="abs pill pill-right" href="#">NEW FLORIST FRANCHISE INQUIRY</a>
  <div class="abs hub"><div class="hub-ring">Lantern<br>Petals</div></div>

  <!-- franchisees -->
  <div class="abs round-photo" role="img" aria-label="Photo of a smiling florist holding a pot of pink flowers" style="left:110px;top:2584px;width:440px;height:440px;background:radial-gradient(circle at 60% 45%,#d9c2b5,#a8474a 55%,#5e4a40)"></div>
  <div class="abs block" style="left:671px;top:2590px;width:417px">
    <div class="eyebrow">Our Franchisees</div>
    <div class="title">Professional Florists</div>
    <div class="rule"></div>
    <div class="copy">
      <p>Lantern Petals brings the best of professional florists and supermarkets together for the benefit of consumers. It supports a national network of owner-operator franchisees, who in many cases are multi-site professional florists, with comprehensive services to enhance franchise profitability. Lantern Petals works with some of the country's largest and most progressive supermarkets to provide franchisee ownership and operation of their strategically important floral departments.</p>
    </div>
    <a class="btn" href="#">VIEW MORE</a>
  </div>

  <!-- features -->
  <div class="abs" role="img" aria-label="Photo of a smiling man in a suit holding a mixed flower bouquet" style="left:455px;top:3080px;width:280px;height:420px;border-radius:140px 140px 0 0;background:linear-gradient(180deg,#e8e2dc,#1f2d4a 45%,#20304e)"></div>
  <div class="abs feature" style="right:737px;top:3131px">Proper Transport
    <div class="icon-circle o"><svg width="50" height="50" viewBox="0 0 50 50" fill="none" stroke="#fff" stroke-width="2.5" stroke-linecap="round"><circle cx="10" cy="10" r="4"/><path d="M18 10h24M8 20h34M8 30h30M8 40h22"/><circle cx="40" cy="40" r="4"/></svg></div>
  </div>
  <div class="abs feature" style="left:721px;top:3131px">
    <div class="icon-circle o"><svg width="50" height="50" viewBox="0 0 50 50" fill="none" stroke="#fff" stroke-width="2.5" stroke-linecap="round" stroke-linejoin="round"><path d="M18 18l6 6 12-14"/><path d="M6 34h10l10 4 16-8"/><path d="M6 42h14l18-4"/></svg></div>Convenience
  </div>
  <div class="abs feature" style="right:805px;top:3278px">Affordable Prices
    <div class="icon-circle g"><svg width="50" height="50" viewBox="0 0 50 50" fill="none" stroke="#fff" stroke-width="2.5" stroke-linecap="round"><circle cx="30" cy="17" r="11"/><path d="M30 10v14M26 13h6a2 2 0 0 1 0 4h-4a2 2 0 0 0 0 4h6"/><path d="M8 30h8v14H8zM16 32h10l8 4v6H16"/></svg></div>
  </div>
  <div class="abs feature" style="left:790px;top:3278px">
    <div class="icon-circle g"><svg width="50" height="50" viewBox="0 0 50 50" fill="none" stroke="#fff" stroke-width="2.5" stroke-linecap="round"><circle cx="12" cy="10" r="4"/><circle cx="25" cy="10" r="4"/><circle cx="38" cy="10" r="4"/><path d="M12 14l13 12M25 14v12M38 14L25 26M25 26v18"/></svg></div>Variety Of Choices
  </div>

  <!-- footer -->
  <svg class="abs" style="left:0;top:3440px" width="1200" height="130" viewBox="0 0 1200 130" aria-hidden="true">
    <path d="M0 120 C200 60 400 40 650 60 C850 76 1000 60 1200 30 L1200 130 L0 130Z" fill="var(--orange)"/>
    <path d="M0 126 C200 74 400 56 650 72 C850 86 1000 72 1200 42 L1200 130 L0 130Z" fill="var(--white)"/>
    <path d="M0 130 L0 110 C200 80 400 66 650 82 C850 96 1000 82 1200 52 L1200 130Z" fill="var(--green)"/>
    <path d="M0 130 L0 124 C200 96 400 82 650 96 C850 110 1000 96 1200 66 L1200 130Z" fill="var(--black)"/>
  </svg>
  <footer class="abs footer">
    <div class="brand"><span class="dot"></span>Lantern Petals</div>
    <div class="foot-nav">
      <span>HOME</span><span class="sep">|</span>
      <span>ABOUT US</span><span class="sep">|</span>
      <span>FOR SUPERMARKETS</span><span class="sep">|</span>
      <span>FOR FRANCHISEES</span><span class="sep">|</span>
      <span>CONTACT</span>
    </div>
    <div class="social">
      <span aria-label="Social link"></span><span aria-label="Social link"></span><span aria-label="Social link"></span>
    </div>
    <div class="copyright">Copyright@2024 - All Rights Reserved BY Lantern Petals</div>
  </footer>

</div>
</body>
</html>
```